Real Estate Business Card

On the front side I want to have my info, my brokerage info.
On the back side I want have my complany’s logo, website and Facebook link. I will provide all this once I select a design.

I would like to see Black background and gold text, Dark Blue and gold text and White and blue text designs

Font styles to use
Sans Serif
Script

```html
<!DOCTYPE html>
<html lang="en">
<head>
<meta charset="utf-8">
<title>Northvale Realty Business Card</title>
<link rel="stylesheet" href="https://fonts.googleapis.com/css2?family=Montserrat:wght@700;800&family=Roboto:wght@400;500&display=swap">
<style>
  :root {
    --page: #2b2b2d;
    --card: #1e1e20;
    --red: #e0363c;
    --tab: #5c6070;
    --gold: #e3bb4b;
    --white: #f2f2f2;
    --slate: #8c95a8;
    --rule: #9a9a9a;
  }
  * { margin: 0; padding: 0; box-sizing: border-box; }
  html, body { width: 1200px; height: 900px; overflow: hidden; }
  body {
    background: var(--page);
    font-family: "Roboto", Arial, sans-serif;
    position: relative;
  }
  .card {
    position: absolute;
    left: 250px;
    width: 700px;
    height: 390px;
    background: var(--card);
    box-shadow: 0 10px 30px rgba(0,0,0,.45);
    overflow: hidden;
  }
  .card--back { top: 45px; }
  .card--front { top: 465px; }
  .edge-stripe {
    position: absolute; left: 0; top: 0; bottom: 0; width: 9px;
    background: var(--red);
  }
  .edge-stripe::before {
    content: ""; position: absolute; left: 0; top: 0; width: 9px; height: 28px;
    background: var(--tab);
  }
  .brand {
    position: absolute;
    display: flex; align-items: center; gap: 12px;
    font-family: "Montserrat", Arial, sans-serif;
    font-weight: 800;
    color: var(--slate);
    letter-spacing: 1px;
  }
  .brand__square { width: 26px; height: 26px; background: var(--red); flex: none; }
  .card--back .brand { right: 50px; bottom: 62px; font-size: 30px; }
  .card--back .brand__square { width: 34px; height: 34px; }
  .card--front .brand { right: 48px; top: 90px; font-size: 30px; }
  .holder { position: absolute; left: 64px; top: 140px; }
  .holder__name {
    font-family: "Montserrat", Arial, sans-serif; font-weight: 700;
    font-size: 25px; color: var(--gold); letter-spacing: .5px;
  }
  .holder__title { font-size: 18px; color: var(--red); margin-top: 2px; letter-spacing: .5px; }
  .divider {
    position: absolute; left: 64px; right: 48px; top: 214px;
    height: 1px; background: var(--rule);
  }
  .contacts { position: absolute; left: 64px; top: 228px; list-style: none; }
  .contacts li {
    display: flex; align-items: center; gap: 12px;
    font-size: 18px; color: var(--white); line-height: 28px;
  }
  .contacts svg { width: 16px; height: 16px; fill: var(--gold); flex: none; }
  .address {
    position: absolute; right: 48px; bottom: 34px;
    text-align: right; font-size: 19px; line-height: 27px;
    font-weight: 500; color: var(--white);
  }
</style>
</head>
<body>
  <section class="card card--back">
    <div class="edge-stripe"></div>
    <div class="brand"><span class="brand__square"></span>NORTHVALE REALTY</div>
  </section>

  <section class="card card--front">
    <div class="edge-stripe"></div>
    <div class="brand"><span class="brand__square"></span>NORTHVALE REALTY</div>

    <div class="holder">
      <h1 class="holder__name">MARA ELLISON</h1>
      <p class="holder__title">CEO/FOUNDER</p>
    </div>

    <div class="divider"></div>

    <ul class="contacts">
      <li><svg viewBox="0 0 16 16"><path d="M3.5 1 6 1.5 7 5 5.3 6.3c.8 1.8 2.2 3.2 4.4 4.4L11 9l3.5 1 .5 2.5-2 2C7 14 2 9 1.5 3z"/></svg>555 214 7730</li>
      <li><svg viewBox="0 0 16 16"><path d="M4 0h8a1 1 0 0 1 1 1v14a1 1 0 0 1-1 1H4a1 1 0 0 1-1-1V1a1 1 0 0 1 1-1zm1 2v10h6V2zm3 11a1 1 0 1 0 0 2 1 1 0 0 0 0-2z"/></svg>555 309 4182</li>
      <li><svg viewBox="0 0 16 16"><path d="M4 1h8v4H4zM1 6h14v7h-3v2H4v-2H1zm4 5v3h6v-3z"/></svg>555 671 2045</li>
      <li><svg viewBox="0 0 16 16"><path d="M1 3h14v10H1zm1.5 1.2L8 8.5l5.5-4.3z"/></svg>mara@northvale.com</li>
    </ul>

    <address class="address" style="font-style:normal">
      1420 Birchwood Road<br>
      Fairbanks, Alaska 99701<br>
      www.northvale.com
    </address>
  </section>
</body>
</html>
```